Design a compelling Tarnwove Business Card that will drive people to my site

I want a business card that I can give to people—less to tell them who I am and more to direct them to my website. My website is a portal for Pelmor Aquatics Officials and a place for people who want to become Pelmor Aquatics Officials.
I am uploading my official company logo as well as a business card mockup that I did on my own. Please feel free to completely stray from this design.
I've included a screen recording of the homepage of my website as well.
Target Market(s)
Pelmor Aquatics Officials and people who desire to become one
Contact Information for Business Card
website url
Look and feel
Each slider illustrates characteristics of the customer's brand and the style your logo design should communicate.

```html
<!DOCTYPE html>
<html lang="en">
<head>
<meta charset="utf-8">
<title>Tarnwove Business Card</title>
<link href="https://fonts.googleapis.com/css2?family=Montserrat:wght@400;600;700&display=swap" rel="stylesheet">
<style>
  :root {
    --brand-blue: #3a55a8;
    --brand-blue-deep: #2f4a9c;
    --accent-light: #9aaddc;
    --name-tint: #aebde8;
    --card-white: #ffffff;
    --backdrop: #e9eaee;
    --text-white: #ffffff;
  }
  * { margin: 0; padding: 0; box-sizing: border-box; }
  html, body {
    width: 1200px; height: 915px; overflow: hidden;
    background: var(--backdrop);
    font-family: "Montserrat", Arial, sans-serif;
  }
  .stage { position: relative; width: 1200px; height: 915px; }
  .card {
    position: absolute; left: 250px; width: 700px; height: 400px;
    border-radius: 26px; overflow: hidden;
    box-shadow: 0 8px 24px rgba(0,0,0,0.18);
  }
  .card-front { top: 38px; background: var(--brand-blue); }
  .card-back { top: 477px; background: var(--brand-blue); }
  .bubble-field {
    position: absolute; inset: 0;
    background: radial-gradient(circle at 70% 25%, rgba(255,255,255,0.10), rgba(255,255,255,0) 55%),
                radial-gradient(circle at 25% 70%, rgba(255,255,255,0.06), rgba(255,255,255,0) 50%);
  }
  .wordmark {
    position: absolute; display: flex; align-items: center; gap: 14px;
    font-weight: 700; letter-spacing: -1px; line-height: 1;
  }
  .wordmark .mark-dot { border-radius: 50%; flex: none; }
  .card-front .wordmark { left: 50%; top: 50%; transform: translate(-50%, -50%); color: var(--text-white); font-size: 78px; }
  .card-front .mark-dot { width: 26px; height: 26px; background: var(--text-white); }
  .back-shape { position: absolute; inset: 0; }
  .card-back .wordmark { left: 52px; top: 168px; color: var(--brand-blue-deep); font-size: 58px; }
  .card-back .mark-dot { width: 20px; height: 20px; background: var(--brand-blue-deep); }
  .contact-block { position: absolute; left: 440px; top: 92px; color: var(--text-white); }
  .contact-name { font-size: 24px; font-weight: 700; color: var(--name-tint); }
  .contact-title { font-size: 16px; font-weight: 400; margin-top: 4px; }
  .contact-rule { width: 26px; height: 1px; background: var(--accent-light); margin: 14px 0 14px; }
  .contact-list { list-style: none; }
  .contact-list li { display: flex; align-items: center; gap: 10px; font-size: 16px; margin-bottom: 13px; }
  .contact-icon { width: 20px; height: 20px; flex: none; }
</style>
</head>
<body>
<main class="stage">
  <section class="card card-front" aria-label="Card front">
    <div class="bubble-field" role="img" aria-label="Soft pattern of translucent water bubbles"></div>
    <div class="wordmark"><span class="mark-dot"></span>tarnwove</div>
  </section>

  <section class="card card-back" aria-label="Card back">
    <svg class="back-shape" width="700" height="400" viewBox="0 0 700 400" aria-hidden="true">
      <circle cx="-20" cy="330" r="420" fill="var(--accent-light)"/>
      <circle cx="-32" cy="330" r="406" fill="var(--card-white)"/>
    </svg>
    <div class="wordmark"><span class="mark-dot"></span>tarnwove</div>
    <div class="contact-block">
      <p class="contact-name">Martin Olsgaard</p>
      <p class="contact-title">CEO &amp; Founder</p>
      <div class="contact-rule"></div>
      <ul class="contact-list">
        <li>
          <svg class="contact-icon" viewBox="0 0 20 20" aria-hidden="true"><circle cx="10" cy="10" r="9" fill="none" stroke="#fff" stroke-width="1.2"/><path d="M7 6l2 2-1 1.2c.6 1.2 1.6 2.2 2.8 2.8L12 11l2 2-1.3 1.3C9.5 14 6 10.5 5.7 7.3z" fill="#fff"/></svg>
          (555) 014-2290
        </li>
        <li>
          <svg class="contact-icon" viewBox="0 0 20 20" aria-hidden="true"><circle cx="10" cy="10" r="9" fill="none" stroke="#fff" stroke-width="1.2"/><rect x="5.5" y="7" width="9" height="6.5" fill="none" stroke="#fff" stroke-width="1.1"/><path d="M5.5 7l4.5 3.5L14.5 7" fill="none" stroke="#fff" stroke-width="1.1"/></svg>
          martin@tarnwove.com
        </li>
        <li>
          <svg class="contact-icon" viewBox="0 0 20 20" aria-hidden="true"><circle cx="10" cy="10" r="9" fill="none" stroke="#fff" stroke-width="1.2"/><circle cx="10" cy="10" r="5" fill="none" stroke="#fff" stroke-width="1"/><path d="M5 10h10M10 5c-2.2 2.8-2.2 7.2 0 10M10 5c2.2 2.8 2.2 7.2 0 10" fill="none" stroke="#fff" stroke-width="0.9"/></svg>
          www.tarnwove.com
        </li>
      </ul>
    </div>
  </section>
</main>
</body>
</html>
```